Law Firm Header Revision

Task: Redesign my law firm Word document header (modern, succinct, logo-first, easy address updates)

I need you to revise and modernize my Microsoft Word document header for Law Office of Bram Holcott, PLLC. The result should look professional and clean on letters (including Letters of Protection), with the logo as the main focus and the text kept succinct.

Goals:
1. Create a modern, minimal header that feels premium and uncluttered.
Make the logo the most visually dominant element.
Reduce the visual weight of the contact/address block so it doesn’t distract from the document.
Make the address easy to change later (I’m moving offices soon) while keeping the same header design.

2. Content to include (keep all info accurate):
Law Office of Bram Holcott, PLLC
615 Pemberly St. Ste #300-214, Houston, TX 77002
Office: 832.555.0143
Direct: 713.555.0187
Fax: 832.555.0129
Bholcottlaw.com

3. Layout requirements:
Provide 3 header style options:
Logo left + contact info right
Centered logo + single concise contact line below
Logo left + firm name prominent + minimal contact line
The primary line near the logo should be minimal (preferably website + main office phone).
The address should be easy to update in one place without redesigning the header. Prefer either:
Move the full address to the footer, or
Put the address in a single dedicated line/block so I can edit it once and keep the layout unchanged.
4. Build constraints:
Must be achievable using standard Microsoft Word tools only (header/footer, tables, alignment, fonts, spacing). No advanced graphics software.
Provide exact header text, plus step-by-step Word instructions for each option:
Font recommendations + sizes
Alignment
Spacing
Table setup (if used)
How to keep it consistent across pages

5. Deliverable:
For each of the 3 options, provide:
The exact header content (with line breaks)
Formatting specs (fonts, sizes, spacing)
Word build steps so I can recreate it reliably and keep the logo as the focal point.

```html
<!DOCTYPE html>
<html lang="en">
<head>
<meta charset="utf-8">
<title>Bram Holcott Law – Letterhead Options</title>
<link href="https://fonts.googleapis.com/css2?family=Roboto:wght@400;500;700&display=swap" rel="stylesheet">
<style>
  :root {
    --navy: #0d1f35;
    --navy-deep: #0a1a2d;
    --board: #d6d6d6;
    --paper: #ffffff;
    --white: #ffffff;
  }
  * { margin: 0; padding: 0; box-sizing: border-box; }
  html, body {
    width: 1200px; height: 520px; overflow: hidden;
    background: var(--board);
    font-family: "Roboto", Arial, sans-serif;
  }
  .board { position: relative; width: 1200px; height: 520px; }

  .sheet {
    position: absolute; top: 40px; width: 340px; height: 440px;
    background: var(--paper);
    box-shadow: 0 4px 14px rgba(0,0,0,0.18);
    overflow: hidden;
  }
  .sheet--angled { left: 37px; }
  .sheet--centered { left: 428px; }
  .sheet--banner { left: 819px; }

  /* brand */
  .brand { position: absolute; display: flex; align-items: center; gap: 4px; }
  .brand__mark { width: 17px; height: 17px; background: var(--navy); }
  .brand__name {
    font-weight: 500; font-size: 11.5px; letter-spacing: 0.2px;
    color: var(--navy); text-transform: uppercase; white-space: nowrap;
  }
  .brand--light .brand__mark { background: var(--white); }
  .brand--light .brand__name { color: var(--white); }

  /* contact rows in headers */
  .contact-row { display: flex; align-items: center; gap: 3px; white-space: nowrap; }
  .contact-row svg { width: 5px; height: 5px; fill: currentColor; flex: none; }
  .contact-row__label { font-size: 4.6px; width: 18px; }
  .contact-row__value { font-size: 5.2px; font-weight: 700; }

  /* option 1 */
  .accent-bar {
    position: absolute; left: 107px; top: 4px; width: 150px; height: 11px;
    background: linear-gradient(90deg, rgba(13,31,53,0) 0%, rgba(13,31,53,0.55) 55%, var(--navy) 100%);
    clip-path: polygon(0 0, 100% 0, 96% 100%, 0 100%);
  }
  .contact-panel {
    position: absolute; left: 250px; top: 0; width: 90px; height: 25px;
    background: var(--navy); color: var(--white);
    clip-path: polygon(10px 0, 100% 0, 100% 100%, 0 100%);
    padding: 5px 6px 0 15px;
    display: flex; flex-direction: column; gap: 2.5px;
  }

  /* option 2 */
  .info-band {
    position: absolute; left: 0; top: 31px; width: 340px; height: 12.5px;
    background: var(--navy); color: var(--white);
    display: flex; justify-content: center; align-items: center; gap: 15px;
    font-size: 5.2px;
  }
  .info-band .contact-row__value { font-size: 5.2px; }
  .info-band__text { font-size: 5.2px; }
  .info-band__rule { position: absolute; left: 0; top: 43px; width: 340px; height: 4px; }

  /* option 3 */
  .header-band {
    position: absolute; left: 0; top: 0; width: 340px; height: 30px;
    background: var(--navy); color: var(--white);
  }
  .header-band__details {
    position: absolute; right: 8px; top: 7px;
    display: flex; align-items: flex-start; gap: 5px;
  }
  .firm-name {
    font-size: 5.2px; font-weight: 700; text-align: right; line-height: 8px;
  }
  .header-band__divider { width: 0.6px; height: 15px; background: rgba(255,255,255,0.7); }
  .header-band__contacts { display: flex; flex-direction: column; gap: 2.5px; padding-top: 1px; }

  /* footer */
  .footer-rule {
    position: absolute; left: 0; top: 398px; width: 340px; height: 3px; background: var(--navy);
  }
  .footer {
    position: absolute; left: 0; top: 403px; width: 340px; height: 37px;
    background: var(--navy); color: var(--white);
  }
  .footer__contacts {
    position: absolute; left: 0; top: 7px; width: 100%; height: 11px;
    display: flex; align-items: center; padding: 0 13px; justify-content: space-between;
  }
  .footer__contacts--centered { justify-content: center; gap: 38px; }
  .footer-item { display: flex; align-items: center; gap: 5px; font-size: 5.8px; white-space: nowrap; }
  .footer-item__icon {
    width: 10px; height: 10px; background: var(--white);
    display: flex; align-items: center; justify-content: center; border-radius: 1px;
  }
  .footer-item__icon svg { width: 6px; height: 6px; fill: var(--navy); }
  .footer__bar {
    position: absolute; left: 0; bottom: 0; width: 100%; height: 16px;
    background: var(--navy-deep);
    display: flex; align-items: center; justify-content: center;
  }
  .footer__title { font-size: 6.6px; font-weight: 700; letter-spacing: 0.1px; }
  .footer__page { position: absolute; right: 15px; font-size: 6.6px; font-weight: 700; }
</style>
</head>
<body>
<svg width="0" height="0" style="position:absolute">
  <defs>
    <symbol id="icon-phone" viewBox="0 0 24 24"><path d="M6.6 10.8a15.2 15.2 0 0 0 6.6 6.6l2.2-2.2c.3-.3.7-.4 1-.2 1.1.4 2.3.6 3.6.6.6 0 1 .4 1 1V20c0 .6-.4 1-1 1A17 17 0 0 1 3 4c0-.6.4-1 1-1h3.5c.6 0 1 .4 1 1 0 1.3.2 2.5.6 3.6.1.3 0 .7-.2 1z"/></symbol>
    <symbol id="icon-pin" viewBox="0 0 24 24"><path d="M12 2a7 7 0 0 0-7 7c0 5.2 7 13 7 13s7-7.8 7-13a7 7 0 0 0-7-7zm0 9.5A2.5 2.5 0 1 1 12 6.5a2.5 2.5 0 0 1 0 5z"/></symbol>
    <symbol id="icon-globe" viewBox="0 0 24 24"><path d="M12 2a10 10 0 1 0 0 20 10 10 0 0 0 0-20zm-1 17.9A8 8 0 0 1 4.1 11H7l2 2v1l2 2zm6.9-2.5A2 2 0 0 0 16 16h-1v-3l-1-1H9V9h2l1-1V6h2a2 2 0 0 0 2-2 8 8 0 0 1 1.9 13.4z"/></symbol>
    <symbol id="icon-fax" viewBox="0 0 24 24"><path d="M7 2h9l3 3v5H7zM3 10h3v12H3zm5 1h13v11H8zm3 3v2h2v-2zm4 0v2h2v-2zm-4 4v2h2v-2zm4 0v2h2v-2z"/></symbol>
  </defs>
</svg>

<main class="board">

  <!-- Option 1: logo left, contact panel right -->
  <section class="sheet sheet--angled" aria-label="Header option one">
    <div class="brand" style="left:9px; top:6px;">
      <span class="brand__mark"></span><span class="brand__name">Bram Holcott</span>
    </div>
    <div class="accent-bar"></div>
    <div class="contact-panel">
      <div class="contact-row"><svg><use href="#icon-phone"/></svg><span class="contact-row__label">Office:</span><span class="contact-row__value">832.555.0143</span></div>
      <div class="contact-row"><svg><use href="#icon-globe"/></svg><span class="contact-row__label">Website:</span><span class="contact-row__value">Bholcottlaw.com</span></div>
    </div>

    <div class="footer-rule"></div>
    <footer class="footer">
      <div class="footer__contacts">
        <div class="footer-item"><span class="footer-item__icon"><svg><use href="#icon-pin"/></svg></span>615 Pemberly St. Ste #300-214, Houston, TX 77002</div>
        <div class="footer-item"><span class="footer-item__icon"><svg><use href="#icon-phone"/></svg></span>Direct: 713.555.0187</div>
        <div class="footer-item"><span class="footer-item__icon"><svg><use href="#icon-fax"/></svg></span>Fax: 832.555.0129</div>
      </div>
      <div class="footer__bar"><span class="footer__title">LETTERS OF PROTECTION</span><span class="footer__page">01</span></div>
    </footer>
  </section>

  <!-- Option 2: centered logo, single contact line -->
  <section class="sheet sheet--centered" aria-label="Header option two">
    <div class="brand" style="left:50%; top:8px; transform:translateX(-50%);">
      <span class="brand__mark"></span><span class="brand__name">Bram Holcott</span>
    </div>
    <div class="info-band">
      <div class="contact-row"><svg><use href="#icon-pin"/></svg><span class="info-band__text">615 Pemberly St. Ste #300-214, Houston, TX 77002</span></div>
      <div class="contact-row"><svg><use href="#icon-phone"/></svg><span class="info-band__text">Office:</span><span class="contact-row__value">832.555.0143</span></div>
      <div class="contact-row"><svg><use href="#icon-globe"/></svg><span class="info-band__text">Website:</span><span class="contact-row__value">Bholcottlaw.com</span></div>
    </div>
    <svg class="info-band__rule" viewBox="0 0 340 4" preserveAspectRatio="none">
      <path d="M33 1 Q170 4 300 1" fill="none" stroke="#0d1f35" stroke-width="0.6"/>
    </svg>

    <div class="footer-rule"></div>
    <footer class="footer">
      <div class="footer__contacts footer__contacts--centered">
        <div class="footer-item"><span class="footer-item__icon"><svg><use href="#icon-phone"/></svg></span>Direct: 713.555.0187</div>
        <div class="footer-item"><span class="footer-item__icon"><svg><use href="#icon-fax"/></svg></span>Fax: 832.555.0129</div>
      </div>
      <div class="footer__bar"><span class="footer__title">LETTERS OF PROTECTION</span><span class="footer__page">01</span></div>
    </footer>
  </section>

  <!-- Option 3: banner with firm name -->
  <section class="sheet sheet--banner" aria-label="Header option three">
    <div class="header-band">
      <div class="brand brand--light" style="left:9px; top:6px;">
        <span class="brand__mark"></span><span class="brand__name">Bram Holcott</span>
      </div>
      <div class="header-band__details">
        <p class="firm-name">Law Office of Bram<br>Holcott, PLLC</p>
        <span class="header-band__divider"></span>
        <div class="header-band__contacts">
          <div class="contact-row"><svg><use href="#icon-phone"/></svg><span class="contact-row__label">Office:</span><span class="contact-row__value">832.555.0143</span></div>
          <div class="contact-row"><svg><use href="#icon-globe"/></svg><span class="contact-row__label">Website:</span><span class="contact-row__value">Bholcottlaw.com</span></div>
        </div>
      </div>
    </div>

    <div class="footer-rule"></div>
    <footer class="footer">
      <div class="footer__contacts">
        <div class="footer-item"><span class="footer-item__icon"><svg><use href="#icon-pin"/></svg></span>615 Pemberly St. Ste #300-214, Houston, TX 77002</div>
        <div class="footer-item"><span class="footer-item__icon"><svg><use href="#icon-phone"/></svg></span>Direct: 713.555.0187</div>
        <div class="footer-item"><span class="footer-item__icon"><svg><use href="#icon-fax"/></svg></span>Fax: 832.555.0129</div>
      </div>
      <div class="footer__bar"><span class="footer__title">LETTERS OF PROTECTION</span><span class="footer__page">01</span></div>
    </footer>
  </section>

</main>
</body>
</html>
```